Infographic representing workforce

Hello - I would like an infographic created to insert into a document to represent the composition of our workforce.
I've attached one very casual idea below but do NOT like the pink! Would prefer something a little more professional / modern.
Here is the information:
TOTAL EMPLOYEES
25
DIVERSITY
White: 60%
Asian: 24%
Hispanic: 8%
Middle-Eastern: 8%
AGE
25 - 44: 32%
45 - 64: 56%
65+: 12%
GENDER
Female: 60%
Male: 40%
EXECUTIVE OFFICERS
2of 3 are women
BOARD COMPOSITION
50% women (3 directors)
One woman from an unrepresented community

```html
<!DOCTYPE html>
<html lang="en">
<head>
<meta charset="utf-8">
<title>Workforce Composition</title>
<link href="https://fonts.googleapis.com/css2?family=Montserrat:wght@500;600;800&display=swap" rel="stylesheet">
<style>
  :root{
    --navy:#0055aa;
    --mid:#0a77b8;
    --light:#7eaed6;
    --pale:#c8dcef;
    --band:#e8f0f8;
    --white:#ffffff;
  }
  html,body{margin:0;padding:0;overflow:hidden;background:var(--white);}
  .canvas{position:relative;width:1200px;height:951px;overflow:hidden;font-family:"Montserrat",sans-serif;color:var(--navy);}
  .title-band{position:absolute;left:0;top:0;width:1200px;height:121px;background:var(--navy);
    display:flex;align-items:center;justify-content:center;}
  .title-band h1{margin:0;color:var(--white);font-weight:800;font-size:90px;letter-spacing:1px;line-height:1;}
  .headcount-band{position:absolute;left:0;top:121px;width:1200px;height:117px;background:var(--band);}
  .headcount-figures{position:absolute;left:97px;top:23px;width:1005px;height:74px;
    background:linear-gradient(90deg,var(--navy),var(--light) 50%,var(--navy));border-radius:6px;opacity:.85;}
  .divider{position:absolute;width:4px;background:var(--light);}
  .pill{position:absolute;height:46px;border-radius:23px;background:var(--navy);color:var(--white);
    font-weight:800;font-size:23px;display:flex;align-items:center;justify-content:center;letter-spacing:-.3px;}
  .charts{position:absolute;left:0;top:0;}
  .tag{position:absolute;font-weight:500;font-size:23px;line-height:26px;padding:0 3px;white-space:nowrap;}
  .tag.dark{background:var(--navy);color:var(--white);}
  .tag.light{background:var(--light);color:var(--white);}
  .tag.pale{background:var(--pale);color:var(--navy);}
  .exec-figures{position:absolute;left:277px;top:711px;width:207px;height:144px;
    background:linear-gradient(90deg,var(--navy) 0 33%,var(--mid) 33%);border-radius:8px;}
  .exec-caption{position:absolute;left:226px;width:320px;top:858px;text-align:center;font-weight:500;font-size:30px;}
  .note{position:absolute;font-weight:500;font-size:18px;line-height:18px;color:var(--navy);}
</style>
</head>
<body>
<div class="canvas">
  <header class="title-band"><h1>TOTAL EMPLOYEES 25</h1></header>
  <div class="headcount-band">
    <div class="headcount-figures" role="img" aria-label="Row of 25 person pictograms: 15 men in dark blue and 10 women in light blue"></div>
  </div>

  <div class="divider" style="left:434px;top:271px;height:334px"></div>
  <div class="divider" style="left:782px;top:271px;height:334px"></div>
  <div class="divider" style="left:596px;top:632px;height:273px"></div>

  <div class="pill" style="left:151px;top:287px;width:183px">DIVERSITY</div>
  <div class="pill" style="left:537px;top:287px;width:146px">GENDER</div>
  <div class="pill" style="left:896px;top:287px;width:89px">AGE</div>
  <div class="pill" style="left:228px;top:645px;width:317px">EXECUTIVE OFFICERS</div>
  <div class="pill" style="left:646px;top:645px;width:306px">BOARD COMPOSITION</div>

  <svg class="charts" width="1200" height="951" viewBox="0 0 1200 951" font-family="Montserrat, sans-serif">
    <!-- Diversity -->
    <g class="diversity-pie" stroke="#fff" stroke-width="2.5" stroke-linejoin="round">
      <path d="M248,447 L327.4,477.4 A85,85 0 1 0 165.9,469 Z" fill="var(--navy)"/>
      <path d="M248,447 L327.4,477.4 A85,85 0 0 1 223.1,528.3 Z" fill="var(--mid)"/>
      <path d="M248,447 L223.1,528.3 A85,85 0 0 1 186.9,506.1 Z" fill="var(--light)"/>
      <path d="M248,447 L186.9,506.1 A85,85 0 0 1 165.9,469 Z" fill="var(--pale)"/>
    </g>
    <g class="diversity-values" font-weight="500" text-anchor="middle">
      <text x="249" y="432" font-size="29" fill="#fff">60%</text>
      <text x="273" y="498" font-size="18" fill="#fff">24%</text>
      <text x="192" y="483" font-size="17" fill="var(--navy)">8%</text>
      <text x="213" y="509" font-size="17" fill="#fff">8%</text>
    </g>
    <g class="leaders" stroke="var(--navy)" stroke-width="1.2" fill="var(--navy)">
      <line x1="297" y1="412" x2="340" y2="412"/><circle cx="297" cy="412" r="2.5"/>
      <line x1="277" y1="512" x2="336" y2="512"/><circle cx="277" cy="512" r="2.5"/>
      <line x1="42" y1="491" x2="187" y2="491"/><circle cx="187" cy="491" r="2.5"/>
      <polyline points="209,515 209,581 387,581" fill="none"/><circle cx="209" cy="515" r="2.5"/>
    </g>

    <!-- Gender -->
    <g class="gender-pie" stroke="#fff" stroke-width="3" stroke-linejoin="round">
      <path d="M608,441 L608,351 A90,90 0 1 1 555.1,513.8 Z" fill="var(--navy)"/>
      <path d="M608,441 L555.1,513.8 A90,90 0 0 1 608,351 Z" fill="var(--mid)"/>
    </g>
    <g class="male-symbol">
      <line x1="565" y1="429" x2="596" y2="397" stroke="#fff" stroke-width="6"/>
      <polyline points="567,397 598,397 598,428" fill="none" stroke="#fff" stroke-width="6"/>
      <circle cx="551" cy="444" r="22" fill="var(--navy)" stroke="#fff" stroke-width="6"/>
      <text x="551" y="448" font-size="11" font-weight="600" fill="#fff" text-anchor="middle">40%</text>
    </g>
    <g class="female-symbol">
      <line x1="648" y1="466" x2="648" y2="505" stroke="#fff" stroke-width="7"/>
      <line x1="631" y1="487" x2="665" y2="487" stroke="#fff" stroke-width="7"/>
      <circle cx="648" cy="441" r="25" fill="var(--navy)" stroke="#fff" stroke-width="7"/>
      <text x="648" y="445" font-size="11" font-weight="600" fill="#fff" text-anchor="middle">60%</text>
    </g>

    <!-- Age -->
    <g class="age-pie" stroke="#fff" stroke-width="2.5" stroke-linejoin="round">
      <path d="M941,447 L885.2,511.2 A85,85 0 1 1 1016.5,407.9 Z" fill="var(--navy)"/>
      <path d="M941,447 L1016.5,407.9 A85,85 0 0 1 1022.8,470.1 Z" fill="var(--light)"/>
      <path d="M941,447 L1022.8,470.1 A85,85 0 0 1 885.2,511.2 Z" fill="var(--mid)"/>
    </g>
    <g class="age-values" font-weight="500" text-anchor="middle">
      <text x="916" y="425" font-size="27" fill="#fff">56%</text>
      <text x="990" y="444" font-size="18" fill="var(--navy)">12%</text>
      <text x="941" y="503" font-size="24" fill="#fff">32%</text>
    </g>
    <g class="leaders" stroke="var(--navy)" stroke-width="1.2" fill="var(--navy)">
      <line x1="966" y1="388" x2="1046" y2="388"/><circle cx="966" cy="388" r="2.5"/>
      <line x1="1016" y1="438" x2="1120" y2="438"/><circle cx="1016" cy="438" r="2.5"/>
      <line x1="982" y1="502" x2="1120" y2="502"/><circle cx="982" cy="502" r="2.5"/>
    </g>

    <!-- Board -->
    <g class="board-pie">
      <path d="M732,713 A84,84 0 0 0 732,881 Z" fill="var(--navy)"/>
      <path d="M736,713 A84,84 0 0 1 736,881 Z" fill="var(--mid)"/>
    </g>
    <g class="leaders" stroke="var(--navy)" stroke-width="1.2" fill="var(--navy)">
      <line x1="798" y1="771" x2="832" y2="771"/><circle cx="798" cy="771" r="2.5"/>
      <line x1="763" y1="855" x2="827" y2="855"/><circle cx="763" cy="855" r="2.5"/>
    </g>
  </svg>

  <div class="tag dark" style="left:340px;top:386px">White</div>
  <div class="tag dark" style="left:336px;top:487px">Asian</div>
  <div class="tag pale" style="left:42px;top:465px">Hispanic</div>
  <div class="tag light" style="left:212px;top:555px">Middle Eastern</div>

  <div class="tag dark" style="left:1046px;top:362px">45-64</div>
  <div class="tag light" style="left:1067px;top:412px">65+</div>
  <div class="tag dark" style="left:1048px;top:477px">25-44</div>

  <div class="exec-figures" role="img" aria-label="Three executive officer pictograms: one man and two women"></div>
  <div class="exec-caption">2 of 3 are Women</div>

  <div class="tag dark" style="left:832px;top:746px">Women</div>
  <div class="note" style="left:832px;top:777px;font-size:19px">50%</div>
  <div class="tag dark" style="left:827px;top:830px">3 Directors</div>
  <div class="note" style="left:825px;top:859px">One woman from an<br>unrepresented community</div>
</div>
</body>
</html>
```